Specialised investor in e-mobility and energy wants business card design

We need a business card design that fits our existing corporate design. <The look and feel must be 'sharp'/'clean', dynamic, communicate momentum, professionalism etc (as one would imagine from a firm in the financial sector). We like the idea of a reverse-side of the card that includes the logo, and the name and contact details on the other. We expect the deliverable to be whatever format might be required to be able to get cards printed directly by a service such as kelmo press. Our website is www.zub.capital

```html
<!DOCTYPE html>
<html lang="en">
<head>
<meta charset="utf-8">
<title>Zub Capital – Business Card</title>
<link rel="stylesheet" href="https://fonts.googleapis.com/css2?family=Questrial&family=Arimo:wght@400;700&display=swap">
<style>
  :root {
    --bg: #1a1c1a;
    --card-dark: #2a4a1d;
    --card-dark-deep: #243f19;
    --leaf: #72a83b;
    --leaf-soft: #7aa642;
    --paper: #f3f4ee;
    --ink-light: #ffffff;
  }
  html, body {
    margin: 0;
    width: 1200px;
    height: 963px;
    overflow: hidden;
    background: var(--bg);
  }
  .sheet {
    position: relative;
    width: 1200px;
    height: 963px;
  }
  .card {
    position: absolute;
    top: 328px;
    width: 520px;
    height: 306px;
    border-radius: 22px;
    overflow: hidden;
    background: linear-gradient(160deg, var(--card-dark), var(--card-dark-deep));
    box-shadow: 0 18px 40px rgba(0,0,0,.55);
  }
  .card--front { left: 50px; }
  .card--back { left: 630px; }

  .wordmark {
    position: absolute;
    display: flex;
    align-items: center;
    gap: 12px;
    font-family: "Questrial", sans-serif;
    color: var(--ink-light);
    letter-spacing: 1px;
    white-space: nowrap;
  }
  .wordmark__dot {
    width: 14px;
    height: 14px;
    border-radius: 50%;
    background: var(--leaf);
  }
  .card--front .wordmark { left: 0; right: 0; top: 92px; justify-content: center; font-size: 46px; }
  .card--back .wordmark { right: 34px; top: 70px; font-size: 44px; }

  .details {
    position: absolute;
    left: 40px;
    right: 30px;
    bottom: 40px;
    display: flex;
    align-items: center;
    font-family: "Arimo", sans-serif;
    color: var(--ink-light);
  }
  .holder { text-align: right; padding-right: 18px; }
  .holder__name { font-weight: 700; font-size: 15px; letter-spacing: .5px; }
  .holder__surname { color: var(--leaf); }
  .holder__place { font-size: 13px; margin-top: 4px; }
  .divider { width: 1px; height: 64px; background: var(--ink-light); opacity: .8; }
  .contacts { list-style: none; margin: 0; padding: 0 0 0 18px; font-size: 13.5px; }
  .contacts li { display: flex; align-items: center; gap: 9px; line-height: 21px; }
  .contacts svg { width: 13px; height: 13px; fill: var(--leaf); }

  .arc { position: absolute; inset: 0; }
</style>
</head>
<body>
<main class="sheet">
  <section class="card card--front" aria-label="Card front">
    <div class="wordmark"><span class="wordmark__dot"></span>Zub Capital</div>
    <div class="details">
      <div class="holder">
        <div class="holder__name">MAREK <span class="holder__surname">ELLWOOD</span></div>
        <div class="holder__place">Geneva, Switzerland</div>
      </div>
      <div class="divider"></div>
      <ul class="contacts">
        <li><svg viewBox="0 0 16 16"><path d="M3.6 1.2l2.3 2.3-1.4 2a9 9 0 0 0 6 6l2-1.4 2.3 2.3-1.5 2.2C7.8 14.7 1.3 8.2 1.4 2.7z"/></svg>+41 79555 0148</li>
        <li><svg viewBox="0 0 16 16"><path d="M1 3h14v10H1zM2 4.2v.3l6 4.3 6-4.3v-.3z"/></svg>marek@zub.capital</li>
        <li><svg viewBox="0 0 16 16"><circle cx="8" cy="8" r="7"/></svg>www.zub.capital</li>
      </ul>
    </div>
  </section>

  <section class="card card--back" aria-label="Card back">
    <svg class="arc" viewBox="0 0 520 306" preserveAspectRatio="none">
      <path d="M0 12 Q310 20 372 306 L0 306 Z" fill="var(--paper)"/>
      <path d="M0 24 Q290 36 350 306 L0 306 Z" fill="var(--leaf-soft)"/>
    </svg>
    <div class="wordmark"><span class="wordmark__dot"></span>Zub Capital</div>
  </section>
</main>
</body>
</html>
```